Brightmill Data Works

Our company is about IT hardwares and IT solutions. IT hardware such as PC, RAMS, storage and servers. IT solutions such as project management, BA. We are also selling new technology too.

Target Market(s)

Consumer, Small to Medium Business, Corporate

Requirements
Must have
• The business card must have the following:
• Name:
• Title:
• Contact Number:
• Email address:
• Website:
• Color: Must match the logo color upgrade

```html
<!DOCTYPE html>
<html lang="en">
<head>
<meta charset="utf-8">
<title>Brightmill Data Works – Business Card</title>
<link rel="stylesheet" href="https://fonts.googleapis.com/css2?family=Barlow:wght@500;700&family=Roboto:wght@400;500&display=swap">
<style>
  :root {
    --page-bg: #e9e6e3;
    --card-white: #fbfbfa;
    --card-dark: #3b3b3c;
    --card-dark-deep: #2e2e2f;
    --orange: #d07a22;
    --orange-deep: #b8651a;
    --ink: #2f3033;
    --ink-soft: #55575b;
    --faint: #f3e6d8;
  }
  * { margin: 0; padding: 0; box-sizing: border-box; }
  html, body {
    width: 1200px; height: 997px; overflow: hidden;
    background: var(--page-bg);
    font-family: "Roboto", Arial, sans-serif;
  }
  .sheet {
    width: 1200px; height: 997px;
    display: flex; flex-direction: column;
    align-items: center; justify-content: center; gap: 56px;
  }
  .card {
    position: relative;
    width: 700px; height: 400px;
    border-radius: 4px;
    overflow: hidden;
    box-shadow: 0 6px 18px rgba(0,0,0,.12);
  }

  /* Front */
  .card-front { background: var(--card-white); }
  .front-watermark {
    position: absolute; left: 60px; top: 40px;
    width: 250px; height: 250px; border-radius: 50%;
    background: var(--faint); opacity: .6;
  }
  .brand {
    position: absolute; left: 70px; top: 150px;
    display: flex; align-items: center; gap: 12px;
  }
  .brand-square { width: 22px; height: 22px; background: var(--orange); }
  .brand-name {
    font-family: "Barlow", Arial, sans-serif; font-weight: 700;
    font-size: 30px; letter-spacing: .5px; color: var(--ink);
    text-transform: uppercase; line-height: 1.05; width: 210px;
  }
  .divider {
    position: absolute; left: 370px; top: 60px;
    width: 2px; height: 170px; background: var(--ink-soft);
  }
  .divider::before {
    content: ""; position: absolute; left: -2px; top: 0;
    width: 6px; height: 40px; background: var(--orange);
  }
  .contact { position: absolute; left: 400px; top: 66px; }
  .person-name {
    font-family: "Barlow", Arial, sans-serif; font-weight: 500;
    font-size: 26px; color: var(--orange); text-transform: uppercase; letter-spacing: .5px;
  }
  .person-title {
    font-family: "Barlow", Arial, sans-serif; font-weight: 700;
    font-size: 15px; color: var(--ink); margin-top: 2px; margin-bottom: 16px;
  }
  .contact-list { list-style: none; }
  .contact-list li {
    display: flex; align-items: center; gap: 9px;
    font-size: 14px; color: var(--ink-soft); line-height: 22px;
  }
  .contact-list svg { width: 12px; height: 12px; fill: var(--orange); flex: none; }
  .front-band { position: absolute; left: 0; bottom: 0; width: 700px; height: 120px; }

  /* Back */
  .card-back {
    background: linear-gradient(135deg, var(--card-dark) 0%, var(--card-dark-deep) 100%);
  }
  .back-pattern {
    position: absolute; inset: 0;
    background: radial-gradient(circle at 50% 50%, #474748 0%, var(--card-dark) 55%, var(--card-dark-deep) 100%);
  }
  .back-brand {
    position: absolute; inset: 0;
    display: flex; align-items: center; justify-content: center;
    font-family: "Barlow", Arial, sans-serif; font-weight: 700;
    font-size: 26px; letter-spacing: 1px; color: var(--orange); text-transform: uppercase;
  }
</style>
</head>
<body>
<main class="sheet">
  <section class="card card-front" aria-label="Business card front">
    <div class="front-watermark"></div>
    <div class="brand">
      <span class="brand-square"></span>
      <span class="brand-name">Brightmill Data Works</span>
    </div>
    <div class="divider"></div>
    <div class="contact">
      <p class="person-name">Daniel Mercer</p>
      <p class="person-title">CEO/FOUNDER</p>
      <ul class="contact-list">
        <li><svg viewBox="0 0 24 24"><path d="M6.6 10.8a15 15 0 0 0 6.6 6.6l2.2-2.2a1 1 0 0 1 1-.25 11.4 11.4 0 0 0 3.6.57 1 1 0 0 1 1 1V20a1 1 0 0 1-1 1A17 17 0 0 1 3 4a1 1 0 0 1 1-1h3.5a1 1 0 0 1 1 1c0 1.25.2 2.45.57 3.57a1 1 0 0 1-.25 1z"/></svg>555 214 0873</li>
        <li><svg viewBox="0 0 24 24"><path d="M2 5h20v14H2z M2 5l10 8 10-8" /></svg>daniel@brightmilldata.com</li>
        <li><svg viewBox="0 0 24 24"><circle cx="12" cy="12" r="10"/></svg>www.brightmilldata.com</li>
      </ul>
    </div>
    <svg class="front-band" viewBox="0 0 700 120" aria-hidden="true">
      <path d="M0 78 H200 Q210 78 218 68 L226 58 Q232 52 242 52 H520 Q530 52 536 46 L544 38 Q550 32 560 32 H700 V40 H562 Q554 40 549 45 L540 55 Q533 62 522 62 H244 Q236 62 231 68 L223 78 Q215 88 203 88 H0 Z" fill="var(--orange)"/>
      <path d="M0 98 H205 Q220 98 230 86 L236 78 Q242 70 254 70 H528 Q540 70 548 62 L556 54 Q562 48 572 48 H700" fill="none" stroke="var(--orange-deep)" stroke-width="1.5"/>
      <rect x="0" y="106" width="700" height="14" fill="var(--orange)"/>
    </svg>
  </section>

  <section class="card card-back" aria-label="Business card back">
    <div class="back-pattern" role="img" aria-label="Repeating dark grey monogram pattern"></div>
    <div class="back-brand">Brightmill Data Works</div>
  </section>
</main>
</body>
</html>
```